I need a fresh looking, exciting and loaded design for Full service Restaurant

We need a web design for our restaurant, which offers full service Pakistani and Indian food in PA, USA. Design should be elegant, simplified so customers can navigate easily and order food online for catering as well as delivery. We need loads of pictures and room to grow. I already have a web address via vemrilo.com. It should include SSL and e-commerce for ordering food.
Be original and be creative and make it a fun site :)

```html
<!DOCTYPE html>
<html lang="en">
<head>
<meta charset="utf-8">
<title>Saffron Lane – Pakistani &amp; Indian Cuisine</title>
<link rel="stylesheet" href="https://fonts.googleapis.com/css2?family=Satisfy&family=Open+Sans:wght@400;600&family=Oswald:wght@400&display=swap">
<style>
:root{
  --red:#cf2e2a;
  --red-dark:#8e1414;
  --green:#4d8a2c;
  --green-dark:#2d6a12;
  --ink:#1f1f1f;
  --charcoal:#262626;
  --header:#e8e8e8;
  --white:#ffffff;
  --muted:#555555;
  --gold:#e6c23a;
}
*{margin:0;padding:0;box-sizing:border-box}
html,body{width:699px;height:1200px;overflow:hidden}
body{position:relative;font-family:"Open Sans",sans-serif;background:var(--white);color:var(--ink)}
.abs{position:absolute}
.script{font-family:"Satisfy",cursive;font-weight:400}

/* header */
.site-header{left:0;top:0;width:699px;height:55px;background:var(--header)}
.brand{left:78px;top:14px;display:flex;align-items:center;gap:6px;font-family:"Satisfy",cursive;font-size:20px;color:var(--red)}
.brand-dot{width:18px;height:18px;border-radius:50%;background:var(--green-dark)}
.main-nav{top:22px;left:0;width:699px;font-family:"Satisfy",cursive;font-size:12px;color:var(--ink)}
.main-nav span{position:absolute;white-space:nowrap}
.main-nav .active{color:var(--red)}
.main-nav .active::after{content:"";position:absolute;left:0;right:0;top:18px;height:2px;border-radius:2px;background:var(--red)}

/* hero */
.hero{left:0;top:55px;width:699px;height:315px;background:radial-gradient(ellipse at 30% 40%,#e39a3a 0%,#c67a2e 30%,#e8d9c0 62%,#b99a78 100%)}
.hero-card{left:194px;top:124px;width:320px;height:144px;border-radius:4px;background:rgba(20,14,10,.78);text-align:center;color:var(--white)}
.hero-title{position:absolute;top:52px;width:100%;font-size:28px;line-height:34px}
.hero-text{position:absolute;top:90px;left:30px;right:30px;font-size:13.5px;line-height:20px}
.hero-arrow{width:22px;height:22px;top:187px;background:#151515;border-radius:2px}
.hero-arrow svg{display:block;margin:6px auto}

/* welcome strip */
.dark-band{left:0;top:370px;width:699px;height:378px;background:radial-gradient(ellipse at 50% 45%,#2c2c2c,#1a1a1a)}
.welcome-frame{left:78px;top:334px;width:543px;height:71px;background:var(--white);border-radius:5px}
.welcome{left:83px;top:341px;width:356px;height:57px;background:linear-gradient(90deg,#c81e1e,#6a0e0e 60%,#1b0808);border-radius:2px;color:var(--white)}
.welcome-badge{position:absolute;left:14px;top:12px;width:32px;height:32px;border-radius:50%;background:rgba(255,255,255,.9)}
.welcome h2{position:absolute;left:64px;top:8px;font-family:"Satisfy",cursive;font-weight:400;font-size:17px;color:var(--gold);white-space:nowrap}
.welcome p{position:absolute;left:65px;top:33px;font-size:6.5px;white-space:nowrap}
.welcome p em{color:#7bc043}
.delivery{left:446px;top:341px;width:170px;height:57px;background:var(--green);border-radius:2px;text-align:center;color:var(--white)}
.delivery h2{font-family:"Satisfy",cursive;font-weight:400;font-size:16px;color:var(--gold);margin-top:8px}
.delivery p{font-family:"Oswald",sans-serif;font-size:15px;margin-top:1px}

/* featured dishes */
.section-title{left:0;width:699px;text-align:center;color:var(--red)}
.best-title{top:422px;font-size:25px}
.divider{top:466px;width:52px;height:1px;background:#555}
.dish{border-radius:50%;border:4px solid var(--white);box-shadow:0 2px 6px rgba(0,0,0,.5)}
.dish-s{width:80px;height:80px;top:502px}
.dish-l{width:110px;height:110px;top:487px;left:295px;border-width:5px}
.flag{left:341px;top:589px;width:18px;height:18px;border-radius:50%;overflow:hidden;border:1px solid #ddd}
.flag i{display:block;height:33.3%}
.dish-name{top:616px;font-size:24px;color:var(--white)}
.dish-text{left:210px;top:653px;width:280px;text-align:center;font-size:7.5px;line-height:13px;color:var(--white)}
.btn{height:22px;line-height:22px;text-align:center;font-size:6.8px;text-transform:uppercase;color:var(--white);letter-spacing:.2px}
.btn-red{background:var(--red);width:61px;top:693px}

/* order online */
.devices{left:78px;top:756px;width:250px;height:208px;border-radius:14px;background:linear-gradient(135deg,#2a2a2a,#4a3024 45%,#3a4450 100%)}
.order-title{left:348px;top:778px;font-size:22px;line-height:26px;color:var(--red)}
.order-text{left:348px;top:843px;width:268px;font-size:6.3px;line-height:12.7px;color:var(--muted)}
.btn-dark{left:348px;top:917px;width:60px;background:#2f2f2f}

/* footer */
.site-footer{left:0;top:984px;width:699px;height:184px;background:var(--red);color:var(--white)}
.footer-brand{left:78px;top:1026px;display:flex;align-items:center;gap:5px;font-family:"Satisfy",cursive;font-size:17px;color:var(--white)}
.footer-brand .brand-dot{background:var(--white);width:15px;height:15px}
.footer-about{left:77px;top:1057px;width:130px;font-size:7.2px;line-height:12.5px;color:var(--white)}
.btn-green{left:78px;top:1124px;width:65px;height:20px;line-height:20px;background:var(--green-dark);border:2px solid #3f8a1f}
.footer-head{top:1014px;font-size:19px;color:var(--white);white-space:nowrap}
.hours{left:223px;top:1052px;font-size:7px;line-height:12.5px;color:var(--white)}
.contact{left:381px;top:1052px;font-size:7px;line-height:12.5px;color:var(--white)}
.contact div{display:flex;gap:5px;align-items:flex-start}
.contact svg{margin-top:2px;flex:none}
.insta{left:507px;top:1056px;display:grid;grid-template-columns:repeat(3,36px);gap:3px}
.insta span{height:26px;border:2px solid var(--white)}

.bottom-bar{left:0;top:1168px;width:699px;height:32px;background:#1d1d1d}
.copyright{left:77px;top:1180px;font-size:6.5px;color:var(--white)}
.copyright b{font-weight:400;color:var(--red)}
.social{left:563px;top:1179px;display:flex;gap:5px}
.social span{width:8px;height:8px;border-radius:50%;background:var(--white)}
</style>
</head>
<body>

<header class="abs site-header">
  <div class="abs brand"><span class="brand-dot"></span>Saffron Lane</div>
  <nav class="abs main-nav">
    <span class="active" style="left:338px">Home</span>
    <span style="left:391px">About us</span>
    <span style="left:453px">Spcial offer</span>
    <span style="left:525px">Delivery</span>
    <span style="left:586px">Contact us</span>
  </nav>
</header>

<section class="abs hero" role="img" aria-label="Close-up photo of chicken biryani with rice and green chilli"></section>
<div class="abs hero-card">
  <div class="hero-title script">Saffron Lane</div>
  <p class="hero-text">We offer full service Pakistani and Indian food in Philadelphia, USA</p>
</div>
<div class="abs hero-arrow" style="left:88px"><svg width="8" height="10" viewBox="0 0 8 10"><path d="M6 1 2 5l4 4" fill="none" stroke="#fff" stroke-width="2"/></svg></div>
<div class="abs hero-arrow" style="left:590px"><svg width="8" height="10" viewBox="0 0 8 10"><path d="M2 1l4 4-4 4" fill="none" stroke="#fff" stroke-width="2"/></svg></div>

<section class="abs dark-band"></section>
<div class="abs welcome-frame"></div>
<div class="abs welcome">
  <span class="welcome-badge"></span>
  <h2>Welcome to Saffron Lane</h2>
  <p>We offer full service Pakistani and Indian food in Philadelphia, USA and <em>READ MORE</em></p>
</div>
<div class="abs delivery">
  <h2>Order Delivery</h2>
  <p>( 01 ) - 555 - 01842</p>
</div>

<h2 class="abs section-title script best-title">Experience The Best food</h2>
<div class="abs divider" style="left:289px"></div>
<div class="abs divider" style="left:359px"></div>

<div class="abs dish dish-s" style="left:82px;background:radial-gradient(#b53a22,#5a1a10)" role="img" aria-label="Tandoori chicken"></div>
<div class="abs dish dish-s" style="left:154px;background:radial-gradient(#d8b060,#8a6a30)" role="img" aria-label="Chicken korma"></div>
<div class="abs dish dish-s" style="left:230px;background:radial-gradient(#e2c79a,#a0603a)" role="img" aria-label="Fried rice"></div>
<div class="abs dish dish-s" style="left:385px;background:radial-gradient(#8a5a48,#3a2018)" role="img" aria-label="Lamb curry"></div>
<div class="abs dish dish-s" style="left:462px;background:radial-gradient(#f0b040,#c07a1a)" role="img" aria-label="Yellow dal curry"></div>
<div class="abs dish dish-s" style="left:536px;background:radial-gradient(#b83a20,#4a5a28)" role="img" aria-label="Beef and vegetable stir fry"></div>
<div class="abs dish dish-l" style="background:radial-gradient(#6a5040,#2a2018)" role="img" aria-label="Vindaloo curry"></div>
<div class="abs flag"><i style="background:#ff9933"></i><i style="background:#fff"></i><i style="background:#138808"></i></div>

<h3 class="abs section-title script dish-name">Vindaloo</h3>
<p class="abs dish-text">An Indian curry made with pork belly is full of aromatic flavors and spices. The traditional Goan food is a must try.</p>
<div class="abs btn btn-red" style="left:285px">Know more</div>
<div class="abs btn btn-red" style="left:355px">Order now</div>

<div class="abs devices" role="img" aria-label="Two smartphones showing the mobile ordering site"></div>
<h2 class="abs script order-title">Order food online for catering<br>as well as Delivery</h2>
<p class="abs order-text">Lorem Ipsum is simply dummy text of the printing and typesetting industry. Lorem Ipsum has been the industry's standard dummy text ever since the 1500s, when an unknown printer took a galley of type and scrambled it to make a type specimen book. It has survived not only five centuries, but also the leap into electronic typesetting, remaining essentially unchanged.</p>
<div class="abs btn btn-dark">View menu</div>

<footer class="abs site-footer"></footer>
<div class="abs footer-brand"><span class="brand-dot"></span>Saffron Lane</div>
<p class="abs footer-about">Lorem Ipsum is simply dummy text of the printing and typesetting industry. Lorem Ipsum has been the industry's standard dummy text ever since the 1500s, when an unknown,...</p>
<div class="abs btn btn-green">Know more</div>

<h3 class="abs script footer-head" style="left:221px">Open Hours</h3>
<div class="abs hours">
  Closed ---------- Sunday<br>
  Monday --------- Friday<br>
  Launch --------- am - 02.30am<br>
  Monday --------- Saturday<br>
  Dinner --------- 05pm - 09pm<br>
  Saturday -------- Dinner Only<br>
  Public Holidays --- 7am - 1am
</div>

<h3 class="abs script footer-head" style="left:378px">Contact us</h3>
<div class="abs contact">
  <div><svg width="6" height="8" viewBox="0 0 6 8"><path d="M3 0a3 3 0 0 0-3 3c0 2 3 5 3 5s3-3 3-5a3 3 0 0 0-3-3z" fill="#fff"/></svg><span>Saffron Lane Rd,<br>Philadelphia, USA</span></div>
  <div><svg width="7" height="7" viewBox="0 0 7 7"><path d="M1 0h1.5l.7 1.8-1 .7a4 4 0 0 0 2.3 2.3l.7-1 1.8.7V6a1 1 0 0 1-1 1A6 6 0 0 1 0 1a1 1 0 0 1 1-1z" fill="#fff"/></svg><span>(01) - 555 - 01843</span></div>
  <div><svg width="7" height="6" viewBox="0 0 7 6"><rect width="7" height="6" fill="#fff"/><path d="M0 0l3.5 3L7 0" fill="none" stroke="#cf2e2a" stroke-width=".8"/></svg><span>hello@saffronlane-mail.com</span></div>
</div>

<h3 class="abs script footer-head" style="left:504px">Instagram</h3>
<div class="abs insta">
  <span style="background:#4a3a2a" role="img" aria-label="Plated dish"></span>
  <span style="background:#b8602a" role="img" aria-label="Fried snacks"></span>
  <span style="background:#8a4a30" role="img" aria-label="Grilled meat"></span>
  <span style="background:#6a5a3a" role="img" aria-label="Plated starter"></span>
  <span style="background:#6a2a22" role="img" aria-label="Sliced steak"></span>
  <span style="background:#a8703a" role="img" aria-label="Spring rolls"></span>
</div>

<div class="abs bottom-bar"></div>
<p class="abs copyright">© 2016 <b>Saffron Lane</b>. All rights reserved.</p>
<div class="abs social"><span></span><span></span><span></span><span></span><span></span></div>

</body>
</html>
```